Business Card Design

Electronic Security
Alarm Systems
CCTV
Electronic Access Control
Security System Integration

Industry/Entity Type

Business

Contact Information for Business Card

Gareth Linwood
PO Box 862
Ashgrove Qld 4071
Phone 07 38526147
Mob 0427395816

```html
<!DOCTYPE html>
<html lang="en">
<head>
<meta charset="utf-8">
<title>VESTA Business Card</title>
<link href="https://fonts.googleapis.com/css2?family=Arimo:wght@400;700&display=swap" rel="stylesheet">
<style>
  :root {
    --bg: #e9e7e4;
    --card: #ffffff;
    --ink: #111111;
    --yellow: #f2cd12;
    --yellow-line: #f0c800;
    --icon-bg: #0d0d0d;
  }
  html, body {
    margin: 0;
    padding: 0;
    width: 1200px;
    height: 960px;
    overflow: hidden;
    background: var(--bg);
    font-family: "Arimo", Arial, sans-serif;
  }
  .card {
    position: absolute;
    left: 110px;
    top: 190px;
    width: 980px;
    height: 580px;
    background: var(--card);
    box-shadow: 0 10px 30px rgba(0,0,0,0.18);
    overflow: hidden;
  }
  .brand {
    position: absolute;
    left: 70px;
    top: 150px;
    width: 380px;
    display: flex;
    align-items: center;
    gap: 18px;
  }
  .brand-mark {
    width: 26px;
    height: 26px;
    background: var(--ink);
    flex: none;
  }
  .brand-name {
    font-size: 78px;
    font-weight: 400;
    color: var(--ink);
    letter-spacing: 2px;
    line-height: 1;
  }
  .brand-tagline {
    position: absolute;
    left: 114px;
    top: 250px;
    font-size: 17px;
    color: var(--ink);
    letter-spacing: 0.5px;
  }
  .divider {
    position: absolute;
    left: 470px;
    top: 60px;
    width: 2px;
    height: 300px;
    background: var(--yellow-line);
  }
  .person-name {
    position: absolute;
    left: 520px;
    top: 52px;
    font-size: 40px;
    font-weight: 700;
    color: var(--ink);
    word-spacing: 14px;
  }
  .contacts {
    position: absolute;
    left: 520px;
    top: 150px;
    margin: 0;
    padding: 0;
    list-style: none;
  }
  .contact {
    display: flex;
    align-items: flex-start;
    gap: 40px;
    margin-bottom: 22px;
    font-size: 23px;
    color: var(--ink);
    line-height: 1.15;
  }
  .contact svg {
    flex: none;
    width: 30px;
    height: 30px;
    margin-top: 22px;
  }
  .stripes {
    position: absolute;
    left: 0;
    right: 0;
    top: 406px;
    height: 8px;
    background: var(--yellow);
  }
  .band {
    position: absolute;
    left: 0;
    right: 0;
    top: 424px;
    bottom: 0;
    background: var(--yellow);
    display: flex;
    flex-direction: column;
    justify-content: center;
    align-items: center;
    font-size: 27px;
    color: var(--ink);
    line-height: 1.25;
    text-align: center;
  }
</style>
</head>
<body>
  <div class="card">
    <div class="brand">
      <span class="brand-mark"></span>
      <span class="brand-name">VESTA</span>
    </div>
    <div class="brand-tagline">Vested Electronic Security Team</div>

    <div class="divider"></div>

    <div class="person-name">Gareth Linwood</div>

    <ul class="contacts">
      <li class="contact">
        <svg viewBox="0 0 30 30" aria-hidden="true">
          <rect width="30" height="30" fill="var(--icon-bg)"/>
          <path d="M8 11 q7 -5 14 0 l-2 3 h-3 v-2 h-4 v2 h-3z" fill="var(--yellow)"/>
          <rect x="9" y="15" width="12" height="8" rx="1" fill="var(--yellow)"/>
        </svg>
        <span>07 38526147</span>
      </li>
      <li class="contact">
        <svg viewBox="0 0 30 30" aria-hidden="true">
          <rect width="30" height="30" fill="var(--icon-bg)"/>
          <rect x="10" y="6" width="10" height="18" rx="2" fill="var(--yellow)"/>
          <rect x="12" y="9" width="6" height="9" fill="var(--icon-bg)"/>
        </svg>
        <span>0427395816</span>
      </li>
      <li class="contact">
        <svg viewBox="0 0 30 30" aria-hidden="true">
          <rect width="30" height="30" fill="var(--icon-bg)"/>
          <path d="M6 15 L15 7 L24 15 H21 V23 H9 V15 Z" fill="var(--yellow)"/>
          <rect x="13" y="17" width="4" height="6" fill="var(--icon-bg)"/>
        </svg>
        <span>PO Box 862<br>Ashgrove Qld 4071</span>
      </li>
    </ul>

    <div class="stripes"></div>
    <div class="band">
      <span>Electronic Security , Alarm Systems , Electronic Access Control</span>
      <span>CCTV , Security System Integration</span>
    </div>
  </div>
</body>
</html>
```